Kelumo.cn needs pages to be re-designed

www.kelumo.cn is our current new site which was launched in April.
We're a financial services website in the crowdfunding space in China to connect borrower's and lender's.

test.kelumo.cn is our test site
u: test
p: newtest
http://test.kelumo.cn/
http://test.kelumo.cn/user/accounts/new_lender
http://test.kelumo.cn/user/accounts/new_borrower
http://test.kelumo.cn/introductions/protection
http://test.kelumo.cn/introductions
http://test.kelumo.cn/introductions/kelumo_admin
http://test.kelumo.cn/introductions/contact
Some of the pages have pop-ups in the bloc's of the pages. Please click the links, to see more content.

User's currently criticize the website for being:
- Too Western looking
- Too simple, too little content
- Content NOT in the pop-ups are too simple
- Pictures are too big and too much blank space
- Relevant information is not there when needed
- The pictures are too generic

What we would like to do is re-design those pages with the same color scheme and style to be more compelling, efficient, non-intimidating and easy-to-use. Our audience is Ages 25-35 predominantly male investors.
We are looking for more ideas to make the content match the style, while bridging western and chinese design. Our ultimate goal is to increase registrants to the website and highlight our core competitive advantages.

Some competitors websites are:
www.fobuxiqi.com
www.tamev.com
www.zzzlendo.com

Reason: Not enough good designs that follow the prompt. Same style, better information layout!

Reason: Still have not received a design we're satisfied with

Reason: WE DONT WANT A COMPLETE REDESIGN OF PAGES . KEEP THE EXACT SAME COLOR AND STYLE - WE WANT CONTENT RE-DESIGN! THE BLOCS ARE TOO SIMPLE - WE WANT MORE CONTENT INSIDE.

Reason: no new designs

Reason: no new designs

Reason: other non-registered pages need to be re-designed

```html
<!DOCTYPE html>
<html lang="zh-CN">
<head>
<meta charset="utf-8">
<title>Kelumo.cn 首页</title>
<link href="https://fonts.googleapis.com/css2?family=Noto+Sans+SC:wght@400;500;700&display=swap" rel="stylesheet">
<style>
:root{
  --green:#6cb33f;
  --green-dark:#4f9a28;
  --blue:#2a9fd8;
  --dark:#3b3b3b;
  --text:#444;
  --muted:#999;
  --line:#e2e2e2;
  --soft:#f3f3f1;
  --white:#fff;
}
*{box-sizing:border-box;margin:0;padding:0}
html,body{width:1200px;height:4139px;overflow:hidden}
body{font-family:"Noto Sans SC",sans-serif;color:var(--text);background:var(--white);font-size:16px}
.wrap{width:1140px;margin:0 auto;position:relative}

/* header */
.site-header{height:110px;background:var(--white);border-bottom:1px solid var(--line)}
.site-header .wrap{display:flex;align-items:center;justify-content:space-between;height:110px}
.brand{display:flex;align-items:center;gap:14px}
.brand-dot{width:46px;height:46px;border-radius:50%;background:var(--green)}
.brand-name{font-size:34px;font-weight:700;color:var(--dark)}
.brand-sub{font-size:13px;color:var(--muted);margin-top:-4px}
.main-nav{display:flex;gap:34px;font-size:17px}
.main-nav a{color:var(--text);text-decoration:none;display:flex;align-items:center;gap:8px}
.main-nav a i{width:18px;height:18px;border-radius:4px;background:#bbb;display:inline-block}
.main-nav a.active{color:var(--green)}
.main-nav a.active i{background:var(--green)}

/* hero */
.hero{height:460px;background:linear-gradient(180deg,#1c6fb8 0%,#4aa3e0 45%,#b8def5 75%,#5d8a45 100%)}
.feature-tabs{height:60px;background:var(--dark);display:flex;justify-content:center}
.feature-tabs li{list-style:none;width:228px;display:flex;align-items:center;justify-content:center;gap:12px;color:var(--white);font-size:26px}
.feature-tabs li svg{width:26px;height:26px}
.feature-tabs li.active{background:var(--green)}
.tab-caption{height:26px;background:var(--green);text-align:center;color:#e8f5df;font-size:13px;line-height:26px}

/* notice + stats */
.notice{height:56px;display:flex;align-items:center;justify-content:center;gap:120px;font-size:15px;border-bottom:1px solid var(--line)}
.notice .more{border:1px solid var(--blue);color:var(--blue);border-radius:14px;padding:2px 18px;font-size:13px}
.ticker{height:44px;display:flex;align-items:center;justify-content:center;gap:30px;font-size:14px;color:var(--green);border-bottom:1px solid var(--line)}
.ticker b{color:var(--text);font-weight:400}
.summary{height:104px;display:flex;align-items:center;gap:48px;padding-left:180px;border-bottom:1px solid var(--line)}
.summary .stat b{display:block;font-size:34px;font-weight:500;color:var(--blue)}
.summary .stat span{font-size:13px;color:var(--muted)}
.summary .sep{width:1px;height:60px;background:var(--line)}
.btn-start{margin-left:40px;background:var(--blue);color:var(--white);font-size:30px;padding:12px 50px 12px 80px;border-radius:30px;position:relative}
.btn-start::before{content:"";position:absolute;left:14px;top:10px;width:52px;height:52px;border-radius:50%;background:var(--white)}

/* loan list */
.list-tabs{margin-top:30px;display:flex;border-bottom:2px solid var(--green);width:1140px;margin-left:30px}
.list-tabs span{padding:10px 30px;font-size:22px;color:var(--text)}
.list-tabs span.active{border:1px solid var(--line);border-bottom:none;color:var(--green);background:var(--white)}
.loans{width:1140px;margin:10px auto 0}
.loan{height:192px;border:1px solid var(--line);margin-bottom:8px;padding:18px 24px;position:relative;background:var(--white)}
.loan h3{font-size:18px;font-weight:500;color:var(--dark);margin-bottom:12px}
.loan .cols{display:flex}
.loan .col{width:210px}
.loan .col small{display:block;font-size:13px;color:var(--muted)}
.loan .col strong{font-size:32px;font-weight:400;color:var(--green)}
.loan .col strong em{font-size:16px;font-style:normal;color:var(--text)}
.loan .meta{font-size:13px;color:var(--muted);margin-top:6px;line-height:22px}
.loan .meta span{color:var(--blue)}
.loan .grade{position:absolute;left:615px;top:70px;font-size:14px;color:var(--muted);line-height:46px}
.loan .grade i{display:inline-block;width:30px;height:30px;border-radius:50%;background:var(--green);color:#fff;font-style:normal;text-align:center;line-height:30px;margin:0 10px 0 24px;vertical-align:middle}
.loan .grade u{display:inline-block;width:30px;height:30px;border-radius:50%;background:#ddd;margin:0 10px 0 24px;vertical-align:middle}
.loan .shield{position:absolute;left:405px;top:122px}
.loan .action{position:absolute;right:30px;top:74px;width:130px;height:38px;border-radius:5px;color:#fff;text-align:center;line-height:38px;font-size:15px;background:var(--blue)}
.loan .action.done{background:#cfcfcf;color:#888}
.loan .stamp{position:absolute;right:230px;top:40px;width:118px;height:118px;border:3px solid var(--green);border-radius:50%;transform:rotate(-18deg);color:var(--green);font-size:22px;font-weight:700;display:flex;align-items:center;justify-content:center;opacity:.8}
.loan .tip{position:absolute;background:#fff;border:1px solid #ccc;box-shadow:0 2px 6px rgba(0,0,0,.15);font-size:11px;color:#777;padding:10px;line-height:16px}

/* section heads */
.sec-head{display:flex;align-items:center;gap:16px;font-size:30px;font-weight:700;color:var(--dark);padding:30px 0 0 80px}
.sec-head::after{content:"";flex:1;height:2px;background:var(--line);margin-right:80px}

/* returns */
.returns{height:410px}
.returns .body{display:flex;padding:30px 80px 0}
.bars{width:480px;height:280px;position:relative;border-bottom:2px solid #ccc}
.bars .lbl{position:absolute;left:0;top:90px;font-size:15px}
.bar{position:absolute;bottom:0;width:64px;background:var(--blue)}
.bar span{position:absolute;top:-24px;width:100%;text-align:center;font-size:14px;color:var(--text)}
.bar.hi{background:var(--green)}
.rtable{margin-left:60px;width:520px;font-size:13px;border-collapse:collapse}
.rtable caption{font-size:17px;color:var(--dark);padding-bottom:12px}
.rtable th,.rtable td{padding:9px 6px;text-align:center;border-bottom:1px solid var(--line);color:var(--muted);font-weight:400}
.rtable td.g{color:var(--green);font-weight:700}
.rtable .bars-row td{padding:6px 4px}
.rtable .bars-row i{display:block;height:12px;background:#777}
.rtable .bars-row i.g{background:var(--green)}

/* insurance */
.insure{height:480px;background:var(--soft)}
.insure .body{display:flex;padding:40px 80px 0}
.partners-box{width:470px}
.partner-names{display:flex;align-items:center;gap:26px;margin-top:20px}
.pname{font-size:28px;font-weight:700;color:var(--dark)}
.partner-names .plus{font-size:30px;color:#888}
.partners-box p{font-size:13px;color:#666;margin-top:18px;line-height:22px}
.partners-box .links{color:var(--blue);font-size:13px;margin-top:10px}
.donut-box{margin-left:60px;width:520px;text-align:center;position:relative}
.donut-box h4{font-size:17px;font-weight:500;color:var(--dark)}
.legend{font-size:12px;color:#666;text-align:left;position:absolute}
.itable{width:100%;border-collapse:collapse;font-size:13px;margin-top:10px}
.itable td{padding:7px;border-bottom:1px solid #ddd;color:#888}

/* examples */
.examples{height:560px}
.examples .body{display:flex;justify-content:space-between;padding:30px 80px 0}
.example{width:500px}
.example h4{font-size:18px;font-weight:500;color:var(--dark);margin-bottom:10px}
.example .frame{border:1px solid var(--line);height:330px;position:relative}

/* control */
.control{height:400px;background:var(--soft)}
.control .body{display:flex;padding:30px 80px 0;justify-content:space-between}
.control p{font-size:20px;line-height:46px;color:var(--dark);margin-top:40px;width:400px}
.shot{width:560px;height:270px;background:linear-gradient(180deg,#e9ecef,#cfd6dc)}

/* steps */
.steps{height:190px;display:flex;justify-content:space-around;padding:30px 100px 0;text-align:center}
.step .ico{width:80px;height:80px;border-radius:50%;border:2px solid #ccc;margin:0 auto 12px;display:flex;align-items:center;justify-content:center}
.step b{font-size:24px;font-weight:500;color:var(--dark);display:block}
.step.blue b{color:var(--blue)}
.step small{font-size:13px;color:var(--muted)}

.partner-row{height:70px;display:flex;align-items:center;gap:40px;padding-left:150px;border-top:1px solid var(--line)}
.partner-row .ptag{font-size:18px;font-weight:700;color:var(--blue)}
.partner-row .pshape{width:90px;height:28px;background:#d8d8d8}
.site-footer{height:49px;background:var(--dark);color:#bbb;font-size:14px;display:flex;align-items:center;padding-left:80px;gap:40px}
.site-footer .icons{margin-left:auto;margin-right:60px;display:flex;gap:16px}
.site-footer .icons i{width:22px;height:22px;border-radius:50%;background:#777}
</style>
</head>
<body>

<header class="site-header">
  <div class="wrap">
    <div class="brand">
      <span class="brand-dot"></span>
      <div><div class="brand-name">Kelumo</div><div class="brand-sub">kelumo.cn</div></div>
    </div>
    <nav class="main-nav">
      <a href="#"><i></i>首页</a><a href="#"><i></i>安全</a><a href="#" class="active"><i></i>借款</a><a href="#"><i></i>新闻</a><a href="#"><i></i>登录 ▾</a>
    </nav>
  </div>
</header>

<section class="hero" role="img" aria-label="蓝天下张开双臂的投资者照片"></section>

<ul class="feature-tabs">
  <li><svg viewBox="0 0 24 24"><circle cx="12" cy="12" r="5" fill="none" stroke="#fff" stroke-width="2"/><path d="M12 1v4M12 19v4M1 12h4M19 12h4" stroke="#fff" stroke-width="2"/></svg>简捷</li>
  <li><svg viewBox="0 0 24 24"><path d="M3 21V12h4v9M10 21V6h4v15M17 21V3h4v18" fill="#fff"/></svg>高回报</li>
  <li class="active"><svg viewBox="0 0 24 24"><path d="M12 2l9 4v6c0 6-4 9-9 10-5-1-9-4-9-10V6z" fill="#fff"/></svg>安全</li>
  <li><svg viewBox="0 0 24 24"><rect x="2" y="4" width="20" height="13" fill="none" stroke="#fff" stroke-width="2"/><path d="M8 21h8" stroke="#fff" stroke-width="2"/></svg>控制</li>
  <li><svg viewBox="0 0 24 24"><path d="M3 7h14l-3-3M21 17H7l3 3" fill="none" stroke="#fff" stroke-width="2"/></svg>转让</li>
</ul>
<div class="tab-caption">本金有保障 全程可追踪 · 资金第三方托管 放心投资</div>

<div class="notice"><span>Kelumo 最新公告：平台运营报告发布</span><span>2014-06-03</span><span class="more">查看全部</span></div>
<div class="ticker">
  <span>成功投资 <b>10000元 年利率 15.0%</b></span><span>成功投资 <b>20000元 年利率 15.0%</b></span><span>成功投资 <b>20000元 年利率 15.0%</b></span><span>成功投资 <b>30000元 年利率 15.0%</b></span>
</div>
<div class="summary">
  <div class="stat"><b>¥56573</b><span>累计成交金额</span></div><div class="sep"></div>
  <div class="stat"><b>14.68%</b><span>平均年化收益</span></div><div class="sep"></div>
  <div class="stat"><b>11.8月</b><span>平均借款期限</span></div>
  <div class="btn-start">开始投资</div>
</div>

<div class="list-tabs"><span class="active">散标列表</span><span>固定产品</span></div>
<div class="loans">
  <div class="loan">
    <h3>短期资金周转</h3>
    <div class="cols">
      <div class="col"><small>融资金额</small><strong>30000<em>元</em></strong></div>
      <div class="col"><small>期限</small><strong>12<em>个月</em></strong></div>
      <div class="col"><small>年化率</small><strong>15.0%</strong></div>
    </div>
    <div class="meta">保障方式 保本金+利息 有风险准备金保障<br>发布日期 <span>2014-10-24</span></div>
    <div class="grade">信用等级<i>A</i><br>投标进度<u></u>0%</div>
    <div class="action">投 标</div>
  </div>
  <div class="loan">
    <h3>经营周转</h3>
    <div class="cols">
      <div class="col"><small>融资金额</small><strong>5431<em>元</em></strong></div>
      <div class="col"><small>期限</small><strong>11<em>个月</em></strong></div>
      <div class="col"><small>年化率</small><strong>15.0%</strong></div>
    </div>
    <div class="meta">保障方式 保本金+利息 有风险准备金保障<br>发布日期 <span>2014-10-24</span></div>
    <svg class="shield" width="24" height="28" viewBox="0 0 24 28"><path d="M12 1l10 4v8c0 7-5 11-10 13C7 24 2 20 2 13V5z" fill="#333"/></svg>
    <div class="tip" style="left:440px;top:56px;width:160px">保险公司承保本金，逾期由合作方先行垫付，全程保障</div>
    <div class="grade">信用等级<i>A</i><br>投标进度<u></u>0%</div>
    <div class="tip" style="left:765px;top:56px;width:160px">每笔借款均经过实地调查，信息真实可查，风险可控</div>
    <div class="action">投 标</div>
  </div>
  <div class="loan">
    <h3>短期经营周转</h3>
    <div class="cols">
      <div class="col"><small>融资金额</small><strong>20000<em>元</em></strong></div>
      <div class="col"><small>期限</small><strong>6<em>个月</em></strong></div>
      <div class="col"><small>年化率</small><strong>15.0%</strong></div>
    </div>
    <div class="meta">保障方式 保本金+利息 有风险准备金保障<br>发布日期 <span>2014-10-24</span></div>
    <svg class="shield" width="24" height="28" viewBox="0 0 24 28"><path d="M12 1l10 4v8c0 7-5 11-10 13C7 24 2 20 2 13V5z" fill="#333"/></svg>
    <div class="grade">信用等级<i>A</i><br>投标进度<u></u>0%</div>
    <div class="stamp">已还款</div>
    <div class="action done">已还款</div>
  </div>
  <div class="loan">
    <h3>短期经营周转</h3>
    <div class="cols">
      <div class="col"><small>融资金额</small><strong>20000<em>元</em></strong></div>
      <div class="col"><small>期限</small><strong>6<em>个月</em></strong></div>
      <div class="col"><small>年化率</small><strong>15.0%</strong></div>
    </div>
    <div class="meta">保障方式 保本金+利息 有风险准备金保障<br>发布日期 <span>2014-10-24</span></div>
    <svg class="shield" width="24" height="28" viewBox="0 0 24 28"><path d="M12 1l10 4v8c0 7-5 11-10 13C7 24 2 20 2 13V5z" fill="#333"/></svg>
    <div class="grade">信用等级<i>A</i><br>投标进度<u></u>0%</div>
    <div class="stamp">已还款</div>
    <div class="action done">已还款</div>
  </div>
  <div class="loan">
    <h3>短期经营周转</h3>
    <div class="cols">
      <div class="col"><small>融资金额</small><strong>20000<em>元</em></strong></div>
      <div class="col"><small>期限</small><strong>6<em>个月</em></strong></div>
      <div class="col"><small>年化率</small><strong>15.0%</strong></div>
    </div>
    <div class="meta">保障方式 保本金+利息 有风险准备金保障<br>发布日期 <span>2014-10-24</span></div>
    <svg class="shield" width="24" height="28" viewBox="0 0 24 28"><path d="M12 1l10 4v8c0 7-5 11-10 13C7 24 2 20 2 13V5z" fill="#333"/></svg>
    <div class="grade">信用等级<i>A</i><br>投标进度<u></u>0%</div>
    <div class="stamp">已还款</div>
    <div class="action done">已还款</div>
  </div>
</div>

<section class="returns">
  <h2 class="sec-head"><svg width="34" height="30" viewBox="0 0 34 30"><path d="M2 28V18h6v10M12 28V10h6v18M22 28V2h6v26" fill="#2a9fd8"/></svg>每年回报率10%-15%</h2>
  <div class="body">
    <div class="bars">
      <span class="lbl">每年回报率10%-15%</span>
      <div class="bar" style="left:170px;height:70px"><span>3.5%</span></div>
      <div class="bar" style="left:250px;height:78px"><span>3.7%</span></div>
      <div class="bar hi" style="left:360px;height:200px"><span>12-15%</span></div>
      <div style="position:absolute;left:370px;top:16px;width:44px;height:44px;border-radius:50%;background:#333"></div>
    </div>
    <table class="rtable">
      <caption>借款能例</caption>
      <tr><th></th><th>定期存款</th><th>活期存款</th><th>理财产品</th><th>信托产品</th><th>股票基金</th></tr>
      <tr><td>年化收益</td><td class="g">10%-15%</td><td>24.4%</td><td>8.13%</td><td>10.21%</td><td>6.8%</td></tr>
      <tr><td>本金保障</td><td class="g">100%</td><td>✓</td><td>✓</td><td>✓</td><td>✓</td></tr>
      <tr><td>流动性</td><td class="g">100%</td><td>✓</td><td>✓</td><td>✓</td><td>✓</td></tr>
      <tr class="bars-row"><td>投资门槛</td><td><i class="g"></i></td><td><i></i></td><td><i></i></td><td><i></i></td><td><i></i></td></tr>
    </table>
  </div>
</section>

<section class="insure">
  <h2 class="sec-head" style="padding-top:40px"><svg width="30" height="34" viewBox="0 0 24 28"><path d="M12 1l10 4v8c0 7-5 11-10 13C7 24 2 20 2 13V5z" fill="#6cb33f"/></svg>每年</h2>
  <div class="body">
    <div class="partners-box">
      <div class="partner-names">
        <span class="pname">恒远保险</span>
        <span class="plus">+</span>
        <span class="pname">Taverin</span>
      </div>
      <p>通过与第一流保险公司合作，为每一位投资者的本金提供全额保障，<br>借款逾期时由保险公司进行赔付，让您安心投资。</p>
      <div class="links">了解合作 &nbsp;&nbsp; 了解安全</div>
    </div>
    <div class="donut-box">
      <h4>借款能例</h4>
      <svg width="200" height="180" viewBox="0 0 200 180" style="margin-top:10px">
        <circle cx="100" cy="90" r="62" fill="none" stroke="#d7d7d7" stroke-width="30"/>
        <circle cx="100" cy="90" r="62" fill="none" stroke="#6cb33f" stroke-width="30" stroke-dasharray="250 390" transform="rotate(-90 100 90)"/>
        <circle cx="100" cy="90" r="62" fill="none" stroke="#2a9fd8" stroke-width="30" stroke-dasharray="70 390" stroke-dashoffset="-250" transform="rotate(-90 100 90)"/>
        <circle cx="100" cy="90" r="26" fill="#333"/>
      </svg>
      <div class="legend" style="left:370px;top:60px">▪ 保险赔付<br><br>▪ 风险准备金<br><br>▪ 借款人还款</div>
      <table class="itable">
        <tr><td>1年期</td><td>100% 保险赔付</td><td>100% 本息保障</td></tr>
        <tr><td>6个月</td><td>100% 保险赔付</td><td>100% 本息保障</td></tr>
        <tr><td>3个月</td><td>100% 保险赔付</td><td>100% 本息保障</td></tr>
      </table>
      <div style="color:var(--blue);font-size:13px;margin-top:10px">了解保险合作详情</div>
    </div>
  </div>
</section>

<section class="examples">
  <h2 class="sec-head"><svg width="32" height="26" viewBox="0 0 24 20"><path d="M2 5h14l-3-3M22 15H8l3 3" fill="none" stroke="#2a9fd8" stroke-width="2.5"/></svg>每年示例文本</h2>
  <div class="body">
    <div class="example">
      <h4>1. 每年示例文本每年示例文本</h4>
      <div class="frame">
        <svg width="500" height="330" viewBox="0 0 500 330">
          <circle cx="60" cy="90" r="22" fill="#bbb"/><text x="36" y="140" font-size="13" fill="#777">投资文本</text>
          <circle cx="60" cy="230" r="22" fill="#bbb"/><text x="36" y="280" font-size="13" fill="#777">投资文本</text>
          <circle cx="250" cy="160" r="30" fill="#333"/><text x="222" y="214" font-size="13" fill="#777">平台文本</text>
          <circle cx="430" cy="160" r="22" fill="#bbb"/><text x="406" y="210" font-size="13" fill="#777">借款文本</text>
          <path d="M90 95L215 145" stroke="#6cb33f" stroke-width="3"/><path d="M90 225L215 175" stroke="#6cb33f" stroke-width="3"/>
          <path d="M290 160h110" stroke="#2a9fd8" stroke-width="3"/><path d="M392 152l10 8-10 8" fill="#2a9fd8"/>
          <text x="130" y="100" font-size="12" fill="#6cb33f">出借</text><text x="130" y="225" font-size="12" fill="#6cb33f">出借</text><text x="330" y="150" font-size="12" fill="#2a9fd8">放款</text>
        </svg>
      </div>
    </div>
    <div class="example">
      <h4>2. 每年示例文本每年示例文本</h4>
      <div class="frame">
        <svg width="500" height="330" viewBox="0 0 500 330">
          <circle cx="60" cy="170" r="22" fill="#bbb"/><text x="36" y="220" font-size="13" fill="#777">投资文本</text>
          <circle cx="250" cy="170" r="30" fill="#333"/>
          <circle cx="430" cy="80" r="22" fill="#bbb"/><circle cx="430" cy="170" r="22" fill="#bbb"/><circle cx="430" cy="260" r="22" fill="#bbb"/>
          <path d="M90 170h120" stroke="#6cb33f" stroke-width="3"/><path d="M202 162l10 8-10 8" fill="#6cb33f"/>
          <path d="M285 155L400 85M290 170h110M285 185L400 255" stroke="#2a9fd8" stroke-width="3"/>
          <text x="210" y="300" font-size="13" fill="#2a9fd8">分散投资文本</text>
        </svg>
      </div>
    </div>
  </div>
</section>

<section class="control">
  <h2 class="sec-head"><svg width="30" height="26" viewBox="0 0 24 20"><rect x="1" y="2" width="22" height="13" fill="none" stroke="#2a9fd8" stroke-width="2.5"/><path d="M7 19h10" stroke="#2a9fd8" stroke-width="2.5"/></svg>始终拥有控制权</h2>
  <div class="body">
    <p>您随时检查您的账户、投资、债务明细<br>更改设置、选择投资方式：手动、自动或<br>我们的固定期限产品。</p>
    <div class="shot" role="img" aria-label="用户账户管理后台界面截图"></div>
  </div>
</section>

<div class="steps">
  <div class="step"><div class="ico"><svg width="40" height="40" viewBox="0 0 40 40"><circle cx="20" cy="22" r="15" fill="none" stroke="#555" stroke-width="3"/><path d="M20 22V13M16 4h8" stroke="#555" stroke-width="3"/></svg></div><b>3分钟内即可完成投资</b><small>注册、验证身份即可开始</small></div>
  <div class="step blue"><div class="ico" style="border-color:var(--blue)"><svg width="40" height="40" viewBox="0 0 40 40"><path d="M4 14L20 5l16 9zM8 16v14M16 16v14M24 16v14M32 16v14M4 33h32" fill="none" stroke="#2a9fd8" stroke-width="3"/></svg></div><b>充值账户</b><small>支持多家银行</small></div>
  <div class="step"><div class="ico"><svg width="40" height="40" viewBox="0 0 40 40"><path d="M16 34V10a3 3 0 016 0v12l8 2v10z" fill="none" stroke="#555" stroke-width="3"/></svg></div><b>选择您的投资方式</b><small>手动投资、固定产品或自动投资</small></div>
</div>

<div class="partner-row">
  <span style="font-size:13px;color:#999">合作伙伴</span>
  <span class="pshape"></span><span class="ptag">NetVeria</span><span class="pshape"></span><span class="pshape"></span><span class="pshape"></span>
</div>

<footer class="site-footer">
  <span>关于我们</span><span>帮助中心</span><span>联系我们</span>
  <div class="icons"><i></i><i></i><i></i><i></i></div>
</footer>

</body>
</html>
```